Fashion clothing business needs a label, swing tag and business card.

Independent womenswear label called "Lottie Vrenn".
I'd like a design for a woven label to go on the clothes, a swing tag and business card design. The design should be simple, modern but timeless. Its a small business, made locally in Melbourne, Australia, produces quality garments for everyday wear using beautiful fabrics.

Target Market(s)

30+ ladies, who want quality everyday wear, who don't necessarily follow trends. They can be a bit edgy and willing to take a risk with something different.

Industry/Entity Type

Clothing

Font styles to use
Other font styles liked:
• I dont mind the typewriter font, but can it look modern? happy for you to choose.

Requirements
Should not have
• A difficult shape swing tag - as it might be more expensive for me to get printed and cut.

```html
<!DOCTYPE html>
<html lang="en">
<head>
<meta charset="utf-8">
<title>Lottie Vrenn – Swing Tag</title>
<link rel="stylesheet" href="https://fonts.googleapis.com/css2?family=Open+Sans:wght@600;700&display=swap">
<style>
  :root {
    --page: #ffffff;
    --tag: #d4d4d5;
    --string: #ebebeb;
    --ink: #111111;
    --rule: #6d6d6d;
  }
  html, body {
    margin: 0;
    padding: 0;
    overflow: hidden;
    background: var(--page);
  }
  .canvas {
    position: relative;
    width: 779px;
    height: 1200px;
    overflow: hidden;
    background: var(--page);
    font-family: "Open Sans", Arial, sans-serif;
    color: var(--ink);
  }
  .tag-shape {
    position: absolute;
    inset: 0;
  }
  .field {
    position: absolute;
    left: 251px;
    width: 326px;
    display: flex;
    align-items: flex-end;
    font-size: 22px;
    font-weight: 700;
    line-height: 1;
  }
  .field-label {
    white-space: nowrap;
  }
  .field-line {
    flex: 1;
    border-bottom: 1.5px solid var(--rule);
    margin-left: 3px;
    margin-bottom: 2px;
  }
  .field-size { top: 718px; }
  .field-style { top: 781px; }
  .field-price { top: 844px; }
  .brand-mark {
    position: absolute;
    left: 355px;
    top: 978px;
    width: 110px;
    height: 110px;
    border-radius: 50%;
    background: var(--ink);
  }
  .brand-name {
    position: absolute;
    left: 150px;
    width: 514px;
    top: 1098px;
    text-align: center;
    font-size: 46px;
    font-weight: 600;
    letter-spacing: 3px;
    text-transform: uppercase;
    line-height: 1.2;
  }
  .web-address {
    position: absolute;
    left: 667px;
    top: 1155px;
    transform-origin: 0 0;
    transform: rotate(-90deg);
    font-size: 22px;
    font-weight: 600;
    letter-spacing: 2.4px;
    white-space: nowrap;
    line-height: 1;
  }
</style>
</head>
<body>
<main class="canvas">
  <svg class="tag-shape" width="779" height="1200" viewBox="0 0 779 1200" aria-hidden="true">
    <rect class="tag-card" x="108" y="430" width="605" height="768" rx="42" fill="var(--tag)"/>
    <ellipse class="tag-eyelet" cx="401" cy="560" rx="56" ry="73" fill="var(--page)" stroke="var(--string)" stroke-width="9"/>
    <path class="tag-string" d="M395 512 C380 490 420 525 440 470 C462 400 438 255 520 125 C572 42 640 18 640 72 C640 170 540 300 408 432" fill="none" stroke="var(--string)" stroke-width="5" stroke-linecap="round"/>
  </svg>

  <div class="field field-size"><span class="field-label">Size:</span><span class="field-line"></span></div>
  <div class="field field-style"><span class="field-label">style:</span><span class="field-line"></span></div>
  <div class="field field-price"><span class="field-label">Price:</span><span class="field-line"></span></div>

  <div class="brand-mark" aria-hidden="true"></div>
  <div class="brand-name">Lottie Vrenn</div>

  <div class="web-address">www.lottievrenn.com</div>
</main>
</body>
</html>
```